MRT Property - Business Cards

Looking for a business card & general letterhead, signage etc design for our new logo.

Colours:
000a20
0056a2
00b5ef
0088ce
68cef2

Fonts:
Poppins
Karla

Please keep look and feel of new brand - example in the zip package I sent.

```html
<!DOCTYPE html>
<html lang="en">
<head>
<meta charset="UTF-8">
<title>MRT Property – Business Cards</title>
<link href="https://fonts.googleapis.com/css2?family=Poppins:wght@400;500;600&display=swap" rel="stylesheet">
<style>
  :root {
    --backdrop: #222222;
    --card-navy: #0d1024;
    --brand-dark: #000a20;
    --brand-blue: #0056a2;
    --brand-sky: #00b5ef;
    --brand-mid: #0088ce;
    --brand-light: #68cef2;
    --band-blue: #1356a8;
    --text-light: #e9eef6;
  }
  * { margin: 0; padding: 0; box-sizing: border-box; }
  html, body {
    width: 1200px; height: 780px; overflow: hidden;
    background: var(--backdrop);
    font-family: "Poppins", sans-serif;
  }
  .sheet {
    position: relative; width: 1200px; height: 780px;
    display: flex; align-items: center; justify-content: center; gap: 50px;
  }
  .card {
    position: relative; width: 540px; height: 309px;
    background: var(--card-navy); overflow: hidden;
    box-shadow: 0 18px 40px rgba(0,0,0,.45);
  }

  /* Front */
  .card-front .band { position: absolute; inset: 0; width: 100%; height: 100%; }
  .brand-name {
    position: absolute; left: 40px; top: 58px;
    font-weight: 600; font-size: 34px; line-height: 1.1;
    color: var(--brand-blue); letter-spacing: .5px;
  }
  .brand-mark {
    display: inline-block; width: 18px; height: 18px; border-radius: 50%;
    background: var(--brand-light); margin-right: 10px; vertical-align: 4px;
  }
  .divider {
    position: absolute; left: 262px; top: 40px; width: 1px; height: 150px;
    background: var(--brand-mid); opacity: .8;
  }
  .contact { position: absolute; left: 290px; top: 52px; }
  .person-name {
    font-weight: 500; font-size: 29px; color: var(--brand-blue); line-height: 1.1;
  }
  .person-name .surname { color: var(--brand-mid); font-weight: 400; }
  .person-role { font-size: 13px; color: var(--text-light); margin-top: 2px; }
  .contact-list { list-style: none; margin-top: 16px; }
  .contact-list li {
    display: flex; align-items: center; gap: 8px;
    font-size: 13.5px; color: var(--text-light); line-height: 1.75;
  }
  .contact-list svg { width: 12px; height: 12px; flex: none; }
  .address {
    position: absolute; left: 28px; bottom: 22px;
    font-size: 13px; color: var(--text-light); letter-spacing: .2px;
  }

  /* Back */
  .card-back .pattern-field {
    position: absolute; inset: 0;
    background: linear-gradient(135deg, #121535 0%, #1a1f5a 45%, #1f3f9a 80%, #1d6fd0 100%);
  }
  .card-back .back-brand {
    position: absolute; right: 40px; bottom: 34px;
    font-weight: 600; font-size: 15px; color: var(--brand-light);
  }
  .card-back .back-brand .brand-mark { width: 9px; height: 9px; margin-right: 6px; vertical-align: 1px; }
</style>
</head>
<body>
<main class="sheet">

  <section class="card card-front">
    <svg class="band" viewBox="0 0 540 309" preserveAspectRatio="none" aria-hidden="true">
      <path d="M0 309 L0 260 C110 262 150 232 250 222 C360 212 430 250 540 236 L540 309 Z" fill="var(--band-blue)"/>
      <path d="M0 244 C110 246 150 216 250 206 C360 196 430 234 540 220" fill="none" stroke="var(--brand-light)" stroke-width="3"/>
    </svg>

    <div class="brand-name"><span class="brand-mark"></span>MRT<br>Property</div>
    <div class="divider"></div>

    <div class="contact">
      <div class="person-name">Lachlan <span class="surname">Moore</span></div>
      <div class="person-role">Director</div>
      <ul class="contact-list">
        <li>
          <svg viewBox="0 0 24 24"><path fill="var(--brand-sky)" d="M6.6 10.8a15.1 15.1 0 0 0 6.6 6.6l2.2-2.2a1 1 0 0 1 1-.24 11.4 11.4 0 0 0 3.6.57 1 1 0 0 1 1 1V20a1 1 0 0 1-1 1A17 17 0 0 1 3 4a1 1 0 0 1 1-1h3.5a1 1 0 0 1 1 1c0 1.25.2 2.45.57 3.57a1 1 0 0 1-.25 1z"/></svg>
          +61 2 9000 4815
        </li>
        <li>
          <svg viewBox="0 0 24 24"><circle cx="12" cy="12" r="9" fill="none" stroke="var(--brand-sky)" stroke-width="2.4"/><path d="M3 12h18M12 3c3 3 3 15 0 18M12 3c-3 3-3 15 0 18" fill="none" stroke="var(--brand-sky)" stroke-width="1.8"/></svg>
          www.mrtproperty.com.au
        </li>
        <li>
          <svg viewBox="0 0 24 24"><rect x="2" y="5" width="20" height="14" rx="2" fill="var(--brand-sky)"/><path d="M3 6l9 7 9-7" fill="none" stroke="var(--card-navy)" stroke-width="2"/></svg>
          hello@mrtproperty.com.au
        </li>
      </ul>
    </div>

    <div class="address">Suite 4.12, Level 4, 18 Harbourline Way, Riverton NSW 2199</div>
  </section>

  <section class="card card-back">
    <div class="pattern-field" role="img" aria-label="Repeating brand symbol pattern in deep navy to bright blue"></div>
    <div class="back-brand"><span class="brand-mark"></span>MRT Property</div>
  </section>

</main>
</body>
</html>
```